Letterhead for Kembara Home Physician

Now we have a new logo we need some letterhead. Attached is the new logo and also the information we need to have on it. We have not yet decided on colour but would like to see a version in each to assist in choosing. I have attached one of the logos but do not have high quality version of the other 'ALGPS member' logo. These can be less prominent. Also Kembara Health Care Cooperative Inc. can be less prominent perhaps small font stating "KHP is trading name for the Kembara Health Care Cooperative Inc."

```html
<!DOCTYPE html>
<html lang="en">
<head>
<meta charset="utf-8">
<title>Kembara Home Physician – Letterhead</title>
<link rel="stylesheet" href="https://fonts.googleapis.com/css2?family=Merriweather:wght@400;700&display=swap">
<style>
  :root {
    --brand-red: #e10613;
    --brand-red-light: #f43a5c;
    --ink: #1e1e1e;
    --rule: #222222;
    --paper: #ffffff;
    --watermark: #eeeeee;
    --badge-green: #1f6b2a;
    --badge-blue: #1b4a9c;
  }
  * { box-sizing: border-box; margin: 0; padding: 0; }
  html, body { width: 955px; height: 1200px; overflow: hidden; background: var(--paper); }
  body { font-family: "Merriweather", Georgia, serif; color: var(--ink); }

  .letterhead { position: relative; width: 955px; height: 1200px; background: var(--paper); }

  .masthead {
    position: absolute; left: 0; top: 0; width: 955px; height: 131px;
    background: radial-gradient(ellipse 380px 130px at 50% 45%, var(--brand-red-light), var(--brand-red) 75%);
    display: flex; align-items: center; justify-content: center; gap: 14px;
  }
  .masthead-mark { width: 40px; height: 40px; border-radius: 50%; background: var(--paper); flex: none; }
  .masthead-name {
    color: var(--paper); font-weight: 700; font-size: 25px; line-height: 1.02;
  }
  .masthead-rule { position: absolute; left: 0; top: 137px; width: 955px; height: 4px; background: var(--rule); }

  .watermark {
    position: absolute; left: 230px; top: 400px; width: 500px; height: 500px;
    border-radius: 50%; background: var(--watermark);
  }

  .footer-rule {
    position: absolute; left: 36px; top: 1080px; width: 898px; height: 3px;
    background: linear-gradient(90deg, transparent, var(--rule) 8%, var(--rule) 92%, transparent);
  }
  .member-badge { position: absolute; left: 56px; top: 1126px; width: 50px; height: 44px; background: var(--badge-green); }
  .member-label { position: absolute; left: 44px; top: 1176px; font-size: 9px; letter-spacing: .2px; }
  .accredited-badge {
    position: absolute; left: 140px; top: 1127px; width: 56px; height: 56px; border-radius: 50%;
    background: var(--badge-blue); border: 3px solid #9bb3dd;
  }

  .contact { position: absolute; left: 203px; top: 1098px; font-size: 15.5px; line-height: 30px; white-space: nowrap; }
  .contact-line { display: flex; align-items: center; gap: 6px; }
  .contact-line.small { font-size: 12.5px; }
  .contact-line .big { font-size: 17px; }
  .contact-line .tiny { font-size: 11.5px; }
  .sep { margin: 0 2px; }
  .icon { width: 14px; height: 14px; flex: none; }
</style>
</head>
<body>
<main class="letterhead">
  <header class="masthead">
    <span class="masthead-mark"></span>
    <div class="masthead-name">Kembara<br>Home<br>Physician</div>
  </header>
  <div class="masthead-rule"></div>

  <div class="watermark" role="img" aria-label="Faint brand watermark"></div>

  <div class="footer-rule"></div>
  <div class="member-badge" role="img" aria-label="ALGPS member badge"></div>
  <div class="member-label">ALGPS MEMBER</div>
  <div class="accredited-badge" role="img" aria-label="Accreditation badge"></div>

  <footer class="contact">
    <div class="contact-line">4/18 Banksia Way Kembara NSW 2600<span class="sep">|</span>PO Box 88, Ridgeview NSW 2611</div>
    <div class="contact-line big">
      <svg class="icon" viewBox="0 0 16 16"><path d="M4 1l3 3-2 2c1 2 3 4 5 5l2-2 3 3-2 3C7 15 1 9 1 3z" fill="none" stroke="currentColor" stroke-width="1.4"/></svg>
      02 4100 2345<span class="sep">|</span>
      <svg class="icon" viewBox="0 0 16 16"><path d="M2 10l2-5h8l2 5v3H2z" fill="currentColor"/><circle cx="4.5" cy="13" r="1.6" fill="#fff"/><circle cx="11.5" cy="13" r="1.6" fill="#fff"/></svg>
      02 4100 6789<span class="sep">|</span>
      <svg class="icon" viewBox="0 0 16 16"><path d="M1 6l7-4 7 4v8H1z" fill="currentColor"/><path d="M1 6l7 5 7-5" fill="none" stroke="#fff" stroke-width="1.3"/></svg>
      hello@kembarahome.com.au
    </div>
    <div class="contact-line small">ABN&nbsp; 48 302 117 905<span class="sep">|</span>
      <svg class="icon" viewBox="0 0 16 16"><circle cx="8" cy="8" r="6.5" fill="none" stroke="currentColor" stroke-width="1.4"/><path d="M1.5 8h13M8 1.5c-3 3-3 10 0 13M8 1.5c3 3 3 10 0 13" fill="none" stroke="currentColor" stroke-width="1.1"/></svg>
      <span class="big">www.kembarahome.com.au</span><span class="sep">|</span><span class="tiny">Kembara Health Care Cooperative Inc</span>
    </div>
  </footer>
</main>
</body>
</html>
```